Unternehmen für Ordnung und Sauberkeit am Arbeitsplatz und Produkte zur Produktionsoptimierung benötigt Visitenkarten und Briefpapier
Zielgruppe
Produkte für Ordnung und Sauberkeit am Arbeitsplatz, Organisation von Arbeitsplätzen, Produkte zur Vereinfachung von Arbeitsabläufen, Produkte zur Produktionsoptimierung unter dem Lean Gedanke, Schlagwort: "5S", nachhaltig, sauber
Aufgabenstellung
Wir sind auf der Suche nach Visitenkarten und Briefpapier für das Unternehmen yourTidor. Nachhaltig, Sauber usw.. Unser Firmenlogo finden Sie anbei.

```html
<!DOCTYPE html>
<html lang="de">
<head>
<meta charset="utf-8">
<title>yourTidor – Visitenkarte</title>
<link rel="stylesheet" href="https://fonts.googleapis.com/css2?family=Open+Sans:wght@400;600;700&display=swap">
<style>
  :root {
    --green: #1a6f34;
    --green-deep: #155d2b;
    --green-light: #3e9a58;
    --grey-panel: #857a71;
    --grey-brand: #8a8a8a;
    --text-light: #f1eeea;
    --icon-bg: #e4e0dc;
    --stage: #e9e7e4;
  }
  * { box-sizing: border-box; margin: 0; padding: 0; }
  html, body { width: 1200px; height: 824px; overflow: hidden; }
  body {
    background: var(--stage);
    font-family: "Open Sans", sans-serif;
    position: relative;
  }
  .card {
    position: absolute;
    top: 237px;
    width: 540px;
    height: 350px;
    box-shadow: 0 6px 18px rgba(0,0,0,.18);
    overflow: hidden;
  }
  .card--front { left: 40px; background: var(--green); }
  .card--back {
    left: 620px;
    background: radial-gradient(ellipse 60% 55% at 15% 100%, #9fc7aa 0%, var(--green-light) 35%, var(--green) 75%);
  }
  .brand {
    position: absolute;
    display: flex;
    align-items: center;
    gap: 12px;
    color: var(--grey-brand);
    font-weight: 700;
    letter-spacing: -0.5px;
    white-space: nowrap;
  }
  .brand__square {
    background: #3a9a4c;
    border-radius: 6px;
    flex: none;
  }
  .card--front .brand { left: 36px; top: 48px; font-size: 62px; }
  .card--front .brand__square { width: 56px; height: 56px; }
  .front__url {
    position: absolute;
    left: 0;
    right: 0;
    top: 200px;
    text-align: center;
    font-size: 34px;
    font-weight: 700;
    color: var(--text-light);
    letter-spacing: 0.5px;
    white-space: nowrap;
  }
  .card--back .brand { left: 36px; top: 146px; font-size: 42px; }
  .card--back .brand__square { width: 38px; height: 38px; }
  .contact-panel {
    position: absolute;
    right: 0; top: 0;
    width: 196px; height: 100%;
    background: var(--grey-panel);
    color: var(--text-light);
    padding: 34px 10px 0 14px;
    font-size: 11.5px;
  }
  .contact-panel__name { font-size: 15px; text-align: center; }
  .contact-panel__role { font-size: 11px; text-align: center; margin-bottom: 36px; }
  .contact-list { list-style: none; }
  .contact-list li {
    display: flex; align-items: center; gap: 8px;
    margin-bottom: 10px; line-height: 1.3;
    white-space: nowrap;
  }
  .contact-icon {
    width: 20px; height: 20px; flex: none;
    background: var(--icon-bg); border-radius: 4px;
    display: flex; align-items: center; justify-content: center;
  }
  .contact-icon svg { width: 13px; height: 13px; }
</style>
</head>
<body>
  <section class="card card--front">
    <div class="brand"><span class="brand__square"></span>yourTidor</div>
    <p class="front__url">www.yourtidor.de</p>
  </section>

  <section class="card card--back">
    <div class="brand"><span class="brand__square"></span>yourTidor</div>
    <aside class="contact-panel">
      <p class="contact-panel__name">Lukas Brenner</p>
      <p class="contact-panel__role">Manager</p>
      <ul class="contact-list">
        <li><span class="contact-icon"><svg viewBox="0 0 16 16"><path d="M8 1a5 5 0 0 0-5 5c0 4 5 9 5 9s5-5 5-9a5 5 0 0 0-5-5z" fill="#1a6f34"/><circle cx="8" cy="6" r="2" fill="#e4e0dc"/></svg></span><span>Lindenweg 12<br>95100 Selbtal</span></li>
        <li><span class="contact-icon"><svg viewBox="0 0 16 16"><path d="M4 2l3 3-2 2a9 9 0 0 0 4 4l2-2 3 3-2 2C6 14 2 10 2 4z" fill="#1a6f34"/></svg></span><span>04821 / 37514 6</span></li>
        <li><span class="contact-icon"><svg viewBox="0 0 16 16"><rect x="3" y="6" width="10" height="7" rx="1" fill="#1a6f34"/><rect x="5" y="2" width="6" height="4" fill="none" stroke="#1a6f34" stroke-width="1.4"/></svg></span><span>04821 / 37514 / 7.2</span></li>
        <li><span class="contact-icon"><svg viewBox="0 0 16 16"><text x="8" y="12.5" text-anchor="middle" font-size="13" font-weight="700" fill="#1a6f34" font-family="Open Sans, sans-serif">@</text></svg></span><span>info@teilwerk-online.de</span></li>
        <li><span class="contact-icon"><svg viewBox="0 0 16 16"><circle cx="8" cy="8" r="6" fill="none" stroke="#1a6f34" stroke-width="1.4"/><ellipse cx="8" cy="8" rx="2.5" ry="6" fill="none" stroke="#1a6f34" stroke-width="1.2"/><line x1="2" y1="8" x2="14" y2="8" stroke="#1a6f34" stroke-width="1.2"/></svg></span><span>www.teilwerk-profis.at</span></li>
      </ul>
    </aside>
  </section>
</body>
</html>
```